Classy, Elegant, Simple Business Card Design

Looking to have a classy, simple, and elegant design. Want a top notch designed business card. I really like the look of the new torvane credit card. I also like the design I attached. I am trying to reach 21-29 year old females for booking us for there wedding or event. We offer Disc Jockey Service, Photo Booth Rentals, and Uplighting .

Target Market(s)

21-28 year old females

Contact Information for Business Card

Has to have logo, website, email, and phone number

Font styles to use
Other font styles liked:
• open to font choice, modern, clean
Designer to choose
33a6d7
0791cd
0555a3
ffffff

Requirements
Must have
• Has to have logo, website, email, and phone number
Nice to have
• I really like the design of the new torvane credit card. I also included my logo and some designs I like
Should not have
• clutter or too much info

```html
<!DOCTYPE html>
<html lang="en">
<head>
<meta charset="utf-8">
<title>Tidewell Event Group – Business Card</title>
<link href="https://fonts.googleapis.com/css2?family=Lato:wght@300;400;700&display=swap" rel="stylesheet">
<style>
  :root {
    --sky: #33a6d7;
    --azure: #0791cd;
    --royal: #0555a3;
    --navy: #123a63;
    --white: #ffffff;
    --ink: #1e2a3a;
    --grey: #9aa3ad;
    --pale: #e6f1f8;
    --backdrop: #d9d9d9;
  }
  * { box-sizing: border-box; margin: 0; padding: 0; }
  html, body { width: 1200px; height: 900px; overflow: hidden; }
  body {
    background: var(--backdrop);
    font-family: "Lato", Arial, sans-serif;
    position: relative;
  }
  .card {
    position: absolute;
    width: 520px;
    height: 300px;
    border-radius: 26px;
    overflow: hidden;
    box-shadow: 0 10px 24px rgba(0,0,0,0.18);
  }
  /* Back side */
  .card-back {
    left: 60px;
    top: 170px;
    background: linear-gradient(180deg, #173b66 0%, #1a74bb 50%, #174c86 100%);
    display: flex;
    align-items: center;
    justify-content: center;
  }
  .card-back .brand-name {
    color: var(--sky);
    font-weight: 700;
    font-size: 46px;
    letter-spacing: 4px;
  }
  /* Front side */
  .card-front {
    left: 620px;
    top: 430px;
    background: var(--white);
  }
  .watermark-name {
    position: absolute;
    right: -10px;
    top: 18px;
    font-weight: 700;
    font-size: 92px;
    color: var(--pale);
    letter-spacing: 2px;
  }
  .brand {
    position: absolute;
    left: 32px;
    top: 92px;
  }
  .brand .brand-name {
    display: flex;
    align-items: center;
    gap: 10px;
    font-weight: 700;
    font-size: 34px;
    color: var(--azure);
    letter-spacing: 3px;
  }
  .brand .brand-dot {
    width: 14px;
    height: 14px;
    border-radius: 50%;
    background: var(--azure);
  }
  .brand .tagline {
    margin-top: 2px;
    margin-left: 24px;
    font-weight: 300;
    font-size: 11px;
    letter-spacing: 7px;
    color: var(--grey);
  }
  .services {
    position: absolute;
    right: 26px;
    top: 92px;
    list-style: none;
    text-align: right;
    font-size: 15px;
    line-height: 1.4;
    color: var(--ink);
  }
  .services li::after {
    content: "";
    display: inline-block;
    width: 8px;
    height: 8px;
    margin-left: 8px;
    border-radius: 50%;
    background: var(--azure);
    vertical-align: middle;
  }
  .contact {
    position: absolute;
    left: 32px;
    bottom: 28px;
    list-style: none;
    font-size: 17px;
    color: var(--ink);
  }
  .contact li {
    display: flex;
    align-items: center;
    gap: 8px;
    line-height: 1.45;
  }
  .contact svg { width: 18px; height: 18px; flex: none; }
</style>
</head>
<body>

<section class="card card-back" aria-label="Card back">
  <span class="brand-name">TIDEWELL</span>
</section>

<section class="card card-front" aria-label="Card front">
  <span class="watermark-name" aria-hidden="true">Tidewell</span>

  <div class="brand">
    <div class="brand-name"><span class="brand-dot"></span>TIDEWELL</div>
    <div class="tagline">EVENT GROUP</div>
  </div>

  <ul class="services">
    <li>Disc Jockey Service</li>
    <li>Photo Booth Rentals</li>
    <li>Uplighting</li>
  </ul>

  <ul class="contact">
    <li>
      <svg viewBox="0 0 20 20" aria-hidden="true"><circle cx="10" cy="10" r="10" fill="#123a63"/><path d="M6.5 5.5l2 0 1 2.5-1.2 1c.6 1.2 1.5 2.1 2.7 2.7l1-1.2 2.5 1v2c0 .6-.5 1-1 1-4 0-7.5-3.5-7.5-7.5 0-.5.4-1.5 1-1.5z" fill="#fff"/></svg>
      044-987 654 321
    </li>
    <li>
      <svg viewBox="0 0 20 20" aria-hidden="true"><circle cx="10" cy="10" r="10" fill="#123a63"/><rect x="5" y="6.5" width="10" height="7" fill="none" stroke="#fff" stroke-width="1.3"/><path d="M5 6.5l5 4 5-4" fill="none" stroke="#fff" stroke-width="1.3"/></svg>
      hello@tidewellevents.com
    </li>
    <li>
      <svg viewBox="0 0 20 20" aria-hidden="true"><circle cx="10" cy="10" r="10" fill="#123a63"/><circle cx="10" cy="10" r="5" fill="none" stroke="#fff" stroke-width="1.2"/><ellipse cx="10" cy="10" rx="2.2" ry="5" fill="none" stroke="#fff" stroke-width="1.1"/><path d="M5 10h10" stroke="#fff" stroke-width="1.1"/></svg>
      www.tidewellevents.com
    </li>
  </ul>
</section>

</body>
</html>
```